Moravel Aesthetic Doctor

I require an elegant, luxurious looking business card for my aesthetic business. I am a doctor and that will set me aside from competitors. I am planning to provide home and spa based treatments to clients with high expectations. I have attached my logo.

```html
<!DOCTYPE html>
<html lang="en">
<head>
<meta charset="UTF-8">
<title>Moravel Aesthetic Doctor – Business Card</title>
<link href="https://fonts.googleapis.com/css2?family=Roboto:wght@300;400&display=swap" rel="stylesheet">
<style>
  :root {
    --stage: #d6d7d9;
    --blue-light: #4ba6da;
    --blue-deep: #0a5fa6;
    --blue-accent: #47a3d8;
    --band-grey: #8d95a3;
    --wave-grey: #9299a6;
    --ink: #2e3440;
    --logo-grey: #8a93a3;
    --white: #ffffff;
    --card-white: #f6f7f8;
  }
  * { box-sizing: border-box; margin: 0; padding: 0; }
  html, body { width: 1200px; height: 576px; overflow: hidden; }
  body {
    background: var(--stage);
    font-family: "Roboto", Arial, sans-serif;
    position: relative;
  }
  .card {
    position: absolute;
    top: 138px;
    width: 484px;
    height: 292px;
    border-radius: 12px;
    overflow: hidden;
    box-shadow: 0 3px 8px rgba(0,0,0,0.18);
  }

  /* Front */
  .card--front {
    left: 82px;
    background: linear-gradient(160deg, var(--blue-light) 0%, #2a84c4 45%, var(--blue-deep) 100%);
    color: var(--white);
  }
  .brand { position: absolute; display: flex; align-items: center; }
  .brand__mark {
    border-radius: 50%;
    flex: none;
  }
  .brand__name { font-weight: 300; line-height: 1; }
  .brand__name .brand__primary { display: block; text-transform: uppercase; letter-spacing: 2px; }
  .brand__name .brand__secondary { display: block; text-transform: uppercase; letter-spacing: 1.5px; margin-top: 8px; }

  .card--front .brand { left: 76px; top: 52px; }
  .card--front .brand__mark { width: 92px; height: 92px; border: 2px solid rgba(255,255,255,0.85); margin-right: 18px; }
  .card--front .brand__name { color: var(--white); }
  .card--front .brand__primary { font-size: 46px; }
  .card--front .brand__secondary { font-size: 19px; }

  .services {
    position: absolute;
    left: 0; right: 0; top: 197px;
    text-align: center;
    font-size: 13px;
    line-height: 18px;
    color: #e8f2fa;
  }
  .services .sep { margin: 0 8px; }
  .tagline-band {
    position: absolute;
    left: 0; right: 0; top: 245px;
    height: 24px;
    background: var(--band-grey);
    text-align: center;
    font-size: 13px;
    line-height: 24px;
    letter-spacing: 1.2px;
    color: #eef1f4;
    font-weight: 300;
  }

  /* Back */
  .card--back {
    left: 602px;
    width: 482px;
    background: linear-gradient(180deg, var(--white) 0%, var(--card-white) 100%);
  }
  .card--back .brand { left: 38px; top: 28px; }
  .card--back .brand__mark { width: 84px; height: 84px; border: 2px solid var(--logo-grey); margin-right: 14px; }
  .card--back .brand__name { color: var(--logo-grey); }
  .card--back .brand__primary { font-size: 42px; }
  .card--back .brand__secondary { font-size: 17px; }

  .waves { position: absolute; left: 0; top: 0; width: 482px; height: 292px; }

  .person { position: absolute; left: 26px; top: 150px; }
  .person__name { font-size: 20px; color: var(--ink); font-weight: 400; }
  .person__post { font-size: 10px; color: var(--blue-accent); margin-left: 6px; letter-spacing: 0.3px; vertical-align: 3px; }
  .person__credential { margin-top: 9px; font-size: 13px; line-height: 16px; color: var(--blue-accent); }

  .contact {
    position: absolute;
    right: 36px; top: 196px;
    list-style: none;
    text-align: right;
    color: var(--white);
    font-size: 12.5px;
  }
  .contact li { display: flex; justify-content: flex-end; align-items: center; height: 19px; }
  .contact li.contact__social { height: 18px; margin-bottom: 6px; }
  .contact .icon { width: 11px; height: 11px; margin-left: 7px; flex: none; }
  .social-dot { width: 11px; height: 11px; border-radius: 50%; background: var(--white); margin-left: 4px; }
  .social-dot:first-of-type { margin-left: 6px; }
</style>
</head>
<body>

  <section class="card card--front" aria-label="Business card front">
    <div class="brand">
      <div class="brand__mark"></div>
      <div class="brand__name">
        <span class="brand__primary">Moravel</span>
        <span class="brand__secondary">Aesthetic Doctor</span>
      </div>
    </div>
    <p class="services">
      Dermal Injectables<span class="sep">|</span>Plasma Facials<span class="sep">|</span>Microneedling<br>
      Skin Boosters<span class="sep">|</span>Excessive Sweating
    </p>
    <div class="tagline-band">HOME AND SPA BASED TREATMENTS</div>
  </section>

  <section class="card card--back" aria-label="Business card back">
    <svg class="waves" viewBox="0 0 482 292" preserveAspectRatio="none" aria-hidden="true">
      <path d="M0,232 C110,262 240,262 330,206 C390,170 440,170 482,176 L482,292 L0,292 Z" fill="#4ba3d6"/>
      <path d="M0,228 C120,270 250,262 340,200 C395,165 445,160 482,166" fill="none" stroke="var(--wave-grey)" stroke-width="6"/>
      <path d="M40,240 C150,268 250,258 330,212" fill="none" stroke="var(--white)" stroke-width="3" opacity="0.9"/>
      <path d="M0,258 C130,290 260,278 345,220" fill="none" stroke="var(--wave-grey)" stroke-width="4" opacity="0.85"/>
      <path d="M0,270 C140,295 270,285 350,235" fill="none" stroke="var(--white)" stroke-width="2" opacity="0.8"/>
    </svg>

    <div class="brand">
      <div class="brand__mark"></div>
      <div class="brand__name">
        <span class="brand__primary">Moravel</span>
        <span class="brand__secondary">Aesthetic Doctor</span>
      </div>
    </div>

    <div class="person">
      <p><span class="person__name">Dr Elena Varsk</span><span class="person__post">MRCPCH MD</span></p>
      <p class="person__credential">Australasian Diploma of<br>Aesthetic Medicine</p>
    </div>

    <ul class="contact">
      <li class="contact__social">Follows:<span class="social-dot"></span><span class="social-dot"></span></li>
      <li>0800 555 014
        <svg class="icon" viewBox="0 0 24 24" aria-hidden="true"><path fill="#fff" d="M6.6 10.8a15 15 0 0 0 6.6 6.6l2.2-2.2c.3-.3.7-.4 1-.2 1.1.4 2.3.6 3.6.6.6 0 1 .4 1 1V20c0 .6-.4 1-1 1A17 17 0 0 1 3 4c0-.6.4-1 1-1h3.5c.6 0 1 .4 1 1 0 1.3.2 2.5.6 3.6.1.3 0 .7-.2 1z"/></svg>
      </li>
      <li>www.moravel.co.nz
        <svg class="icon" viewBox="0 0 24 24" aria-hidden="true"><rect x="2" y="5" width="20" height="14" rx="2" fill="#fff"/><path d="M3 6l9 7 9-7" fill="none" stroke="#4ba3d6" stroke-width="1.6"/></svg>
      </li>
      <li>elena@moravel.co.nz
        <svg class="icon" viewBox="0 0 24 24" aria-hidden="true"><g fill="none" stroke="#fff" stroke-width="2"><circle cx="12" cy="12" r="9.5"/><ellipse cx="12" cy="12" rx="4" ry="9.5"/><path d="M2.5 12h19"/></g></svg>
      </li>
    </ul>
  </section>

</body>
</html>
```